KLW AUDITION

I need a post card design (front only) with this on it:
Bold Rising Steps (this is the main title to be in all caps)
Auditions
Date: Thursday June 30th
6:30-8:30 PM in person
Address: 4172 Fernwick BLVD, Oakland CA 94603
video submissions turn in by Sunday July 3rd, 2022 email:BoldRisingSteps22@tolvamail.com
Teens and Adults welcomed

SO PLEASE COME UP WITH A DESIGN THATS COLORFUL AND INVITING THX!

```html
<!DOCTYPE html>
<html lang="en">
<head>
<meta charset="utf-8">
<title>Bold Rising Steps Auditions – Postcard</title>
<link rel="stylesheet" href="https://fonts.googleapis.com/css2?family=Zilla+Slab:wght@600;700&family=Yellowtail&family=Lato:wght@300;400&family=Roboto+Slab:wght@700&family=Oswald:wght@500;600&family=Kaushan+Script&display=swap">
<style>
  :root {
    --page: #ecebe8;
    --night: #1a1548;
    --indigo: #2b2478;
    --violet: #7a2cc4;
    --magenta: #d23fc8;
    --pink-glow: #f08ae6;
    --yellow: #f7ec1e;
    --white: #ffffff;
    --cream: #f3efd9;
    --band-green: #8fd14f;
    --band-teal: #2fb3a0;
    --band-blue: #3592d9;
    --ink: #0d0a24;
    --pin: #f27a3a;
  }
  * { box-sizing: border-box; margin: 0; padding: 0; }
  html, body { width: 800px; height: 1200px; overflow: hidden; background: var(--page); }

  .postcard {
    position: absolute;
    left: 20px; top: 346px;
    width: 760px; height: 507px;
    overflow: hidden;
    background:
      radial-gradient(ellipse 180px 260px at 545px 40px, rgba(255,255,255,0.55), rgba(255,255,255,0) 70%),
      radial-gradient(ellipse 300px 320px at 560px 220px, rgba(226,70,214,0.9), rgba(226,70,214,0) 75%),
      radial-gradient(ellipse 260px 200px at 330px 60px, rgba(210,63,200,0.55), rgba(210,63,200,0) 75%),
      radial-gradient(ellipse 300px 120px at 520px 470px, rgba(160,90,255,0.6), rgba(160,90,255,0) 75%),
      linear-gradient(100deg, var(--night) 0%, var(--indigo) 35%, var(--violet) 65%, #5a1d8f 100%);
  }
  .stage-floor {
    position: absolute; left: 0; bottom: 0; width: 100%; height: 36px;
    background: linear-gradient(180deg, #120d2e, #05030f);
  }
  .dancer-photo {
    position: absolute; left: 420px; top: 12px; width: 320px; height: 488px;
    border-radius: 40% 40% 12px 12px;
    background: radial-gradient(ellipse at 50% 40%, rgba(196,122,104,0.75), rgba(150,80,90,0.35) 60%, rgba(150,80,90,0) 80%);
  }

  .title {
    position: absolute; left: 43px; top: 50px;
    font-family: "Zilla Slab", serif; font-weight: 700;
    color: var(--white); text-transform: uppercase;
    text-shadow: 0 0 1px var(--ink), 2px 2px 0 var(--ink);
    line-height: 1;
  }
  .title-line { display: block; font-size: 57px; letter-spacing: 1px; }
  .title-line + .title-line { margin-top: 6px; display: flex; align-items: flex-end; }
  .title-sub {
    font-family: "Yellowtail", cursive; font-weight: 400;
    text-transform: none; color: var(--yellow);
    font-size: 40px; letter-spacing: 0; margin-left: 4px; margin-bottom: -8px;
    text-shadow: 1px 1px 0 var(--ink);
  }
  .sparkle { position: absolute; left: 440px; top: 132px; }

  .date-band {
    position: absolute; left: 43px; top: 210px; width: 460px; height: 46px;
    background: linear-gradient(90deg, var(--band-green), var(--band-teal) 60%, var(--band-blue));
    border-top: 2px solid var(--white); border-left: 2px solid var(--white);
    font-family: "Zilla Slab", serif; font-weight: 700; font-size: 30px;
    color: var(--cream); letter-spacing: 2px; padding-left: 24px; line-height: 44px;
    text-shadow: 2px 2px 0 var(--ink);
  }
  .band-post { position: absolute; top: 256px; width: 18px; height: 22px; background: var(--white); }
  .band-post.left { left: 58px; }
  .band-post.right { left: 275px; }
  .time-box {
    position: absolute; left: 43px; top: 278px; width: 263px; height: 31px;
    background: var(--ink); border: 1.5px solid var(--white);
    font-family: "Roboto Slab", serif; font-weight: 700; font-size: 19px;
    color: var(--yellow); text-align: center; line-height: 28px;
  }

  .video-note {
    position: absolute; left: 46px; top: 338px; width: 228px;
    font-family: "Lato", sans-serif; font-weight: 400; font-size: 14px;
    color: var(--white); line-height: 17px; text-transform: uppercase;
  }
  .rule { position: absolute; height: 1px; background: var(--yellow); }
  .deadline {
    position: absolute; left: 46px; top: 384px;
    display: grid; grid-template-columns: auto auto; column-gap: 8px;
    font-family: "Oswald", sans-serif; font-weight: 600; line-height: 1;
  }
  .deadline-day { color: var(--yellow); font-size: 18px; align-self: end; }
  .deadline-date { color: var(--white); font-size: 26px; font-family: "Roboto Slab", serif; }
  .deadline-year { color: var(--white); font-size: 30px; letter-spacing: 1px; }
  .deadline-month {
    background: var(--yellow); color: var(--ink); font-size: 17px;
    align-self: end; padding: 1px 6px; margin-bottom: 2px;
  }

  .address {
    position: absolute; left: 231px; top: 336px;
    display: flex; align-items: center; gap: 9px;
    font-family: "Lato", sans-serif; font-weight: 400; font-size: 14px;
    color: var(--white); line-height: 19px; letter-spacing: 0.5px;
  }
  .email-box {
    position: absolute; left: 231px; top: 380px; width: 250px; height: 23px;
    border: 1px solid var(--white); border-right: none;
    font-family: "Lato", sans-serif; font-size: 12.5px; color: var(--white);
    padding-left: 8px; line-height: 21px; letter-spacing: 0.3px;
  }
  .welcome {
    position: absolute; left: 232px; top: 406px;
    font-family: "Kaushan Script", cursive; font-size: 12px;
    color: var(--yellow); letter-spacing: 2.2px;
  }
</style>
</head>
<body>
  <main class="postcard">
    <div class="dancer-photo" role="img" aria-label="Photo of a ballet dancer in a rose dress posing under a stage spotlight"></div>
    <div class="stage-floor"></div>

    <h1 class="title">
      <span class="title-line">Bold Rising</span>
      <span class="title-line">Steps <span class="title-sub">Auditions</span></span>
    </h1>
    <svg class="sparkle" width="26" height="24" viewBox="0 0 26 24" aria-hidden="true">
      <path d="M9 0 L11 7 L18 9 L11 11 L9 18 L7 11 L0 9 L7 7 Z" fill="#f7ec1e"/>
      <path d="M21 12 L22 15 L25 16 L22 17 L21 20 L20 17 L17 16 L20 15 Z" fill="#f7ec1e"/>
    </svg>

    <div class="date-band">THURSDAY JUNE 30TH</div>
    <div class="band-post left"></div>
    <div class="band-post right"></div>
    <div class="time-box">6:30-8:30 pm in person</div>

    <p class="video-note">Video submissions<br>turn in by</p>
    <div class="rule" style="left:46px; top:375px; width:228px;"></div>
    <div class="deadline">
      <span class="deadline-day">SUNDAY</span>
      <span class="deadline-date">3RD</span>
      <span class="deadline-year">2022</span>
      <span class="deadline-month">JULY</span>
    </div>

    <div class="address">
      <svg width="32" height="34" viewBox="0 0 32 34" aria-hidden="true">
        <path d="M2 28 L10 22 L16 26 L22 22 L30 28 L22 32 L16 29 L10 32 Z" fill="#f7c23a"/>
        <path d="M16 2 C10 2 7 6 7 10 C7 16 16 25 16 25 C16 25 25 16 25 10 C25 6 22 2 16 2 Z" fill="var(--pin)"/>
        <circle cx="16" cy="10" r="4" fill="none" stroke="#fff" stroke-width="2"/>
      </svg>
      <span>4172 Fernwick BLVD,<br>Oakland CA 94603</span>
    </div>
    <div class="email-box">BoldRisingSteps22@tolvamail.com</div>
    <p class="welcome">Teens and Adults welcomed</p>
    <div class="rule" style="left:232px; top:427px; width:204px;"></div>
  </main>
</body>
</html>
```